Flyer for Commercial Roofing Company

We are seeking a talented graphic designer to create a high-quality, visually appealing bifold brochure for Brackenvale Roofing, a certified commercial roofing company specializing in apartment communities. The brochure will be 8.5x11 inches when folded and 17x11 inches when open, containing a front cover, two inside pages, and a back cover. The content is already developed, highlighting our services, key features, and contact information. The design should incorporate professional imagery of multifamily properties, modern icons, a clean layout, and our brand colors and logo to convey trust, expertise, and innovation. The goal is to produce a compelling marketing piece that engages property managers and decision-makers.
Target Market(s)
Apartment Communites
Look and feel
Each slider illustrates characteristics of the customer's brand and the style your logo design should communicate.

```html
<!DOCTYPE html>
<html lang="en">
<head>
<meta charset="utf-8">
<title>Brackenvale Roofing – Bifold Brochure</title>
<link href="https://fonts.googleapis.com/css2?family=Poppins:wght@400;500;600;700;800&family=Alex+Brush&display=swap" rel="stylesheet">
<style>
:root{
  --navy:#2b2d8f;
  --navy-deep:#1b1d3a;
  --red:#b3141c;
  --ink:#2a2a2a;
  --muted:#444;
  --stage:#8c8c8c;
  --sky-top:#6fa8d6;
  --sky-mid:#bcd8ee;
  --sky-low:#eef5fb;
  --white:#ffffff;
}
*{margin:0;padding:0;box-sizing:border-box}
html,body{width:1200px;height:2410px;overflow:hidden}
body{background:var(--stage);font-family:'Poppins',sans-serif;color:var(--ink);position:relative}
.spread{position:absolute;left:50px;width:1100px;height:712px;overflow:hidden;box-shadow:0 10px 30px rgba(0,0,0,.35)}
.spread--outside{top:440px;background:linear-gradient(180deg,var(--sky-top) 0%,var(--sky-mid) 45%,var(--sky-low) 100%)}
.spread--inside{top:1258px;background:var(--white)}
.abs{position:absolute}
.center{text-align:center}
.sky-photo{position:absolute;inset:0}
.frame-lines{position:absolute;inset:0;pointer-events:none}

/* back cover */
.quote-mark{left:60px;width:426px;top:28px;font-size:64px;font-weight:800;color:var(--red);line-height:1}
.quote-text{left:60px;width:426px;top:83px;font-size:15px;line-height:18px;color:var(--ink)}
.quote-author{left:60px;width:426px;top:126px;font-size:14px;font-weight:500;color:var(--navy)}
.script{font-family:'Alex Brush',cursive;color:var(--red)}
.get-in-touch{left:60px;width:426px;top:160px;font-size:40px;line-height:1}
.ready{left:60px;width:426px;top:209px;font-size:15px;font-weight:600;line-height:18px;color:var(--ink)}
.photo{position:absolute;border-radius:6px}
.house-photo{left:150px;top:278px;width:250px;height:240px;background:radial-gradient(ellipse at 50% 45%,#f2f2f2 0%,#9aa0a6 45%,#6c9b4a 70%,rgba(108,155,74,0) 72%)}
.contact-title{left:138px;width:276px;top:546px;font-size:20px;font-weight:700;color:var(--white)}
.contact-icons{left:138px;width:276px;top:584px;display:flex;justify-content:center;gap:4px}
.contact-icons span{width:15px;height:15px;border-radius:50%;background:var(--red);border:1.5px solid var(--white)}
.contact-line{left:138px;width:276px;font-size:14px;color:var(--white)}

/* front cover */
.brand-name{left:600px;width:446px;top:110px;font-size:17px;font-weight:700;color:var(--navy);line-height:20px;letter-spacing:.5px}
.brand-square{left:813px;top:78px;width:22px;height:22px;background:var(--navy)}
.headline{left:600px;width:446px;top:158px;font-size:32px;font-weight:800;line-height:33px}
.headline .dark{color:#3a3a3a}
.headline .red{color:var(--red)}
.with-script{left:600px;width:446px;top:258px;font-size:34px;color:var(--navy);line-height:1}
.subhead{left:600px;width:446px;top:293px;font-size:17px;font-weight:600;line-height:21px;color:#333}
.building-photo{left:588px;top:360px;width:460px;height:210px;background:linear-gradient(180deg,#c8613a 0%,#a9482b 55%,#e8e4dd 56%,#3b3b3b 100%);border-radius:4px}
.seal{left:618px;top:282px;width:120px;height:120px}
.seal-text{left:630px;top:312px;width:96px;font-size:11px;font-weight:600;line-height:13px;color:var(--white)}
.feature{display:flex;align-items:center;gap:8px;top:598px}
.feature-icon{width:30px;height:30px;border-radius:7px;display:flex;align-items:center;justify-content:center}
.feature-icon i{width:12px;height:12px;border:2px solid var(--white);border-radius:50%}
.feature-icon--red{background:var(--red)}
.feature-icon--navy{background:var(--navy)}
.feature-label{font-size:11px;line-height:13px;color:#333}
.site-url{left:600px;width:446px;top:655px;font-size:13px;font-weight:700;letter-spacing:3.5px;color:var(--red)}
.site-url b{color:var(--navy);font-weight:700}

/* inside left */
.section-title{font-size:22px;font-weight:700;line-height:27px;color:var(--ink)}
.section-title .red{color:var(--red)}
.solution{position:absolute;left:42px;width:220px;height:110px}
.solution-photo{position:absolute;left:0;width:88px;height:88px;border-radius:50%;border:2px solid var(--red)}
.solution-name{position:absolute;left:100px;font-size:13px;font-weight:700}
.solution-desc{position:absolute;left:100px;width:120px;font-size:11.5px;line-height:14px;color:var(--muted)}
.blue{color:var(--navy)}
.red{color:var(--red)}
.divider{position:absolute;left:42px;width:216px;height:1px;background:#bdbdbd}
.why-title{left:314px;top:138px;font-size:16px;font-weight:700;line-height:19px;color:var(--ink)}
.why-body{left:314px;top:194px;width:175px;font-size:11.5px;line-height:14px;color:var(--muted)}
.cred{position:absolute;left:314px;width:190px}
.cred-icon{position:absolute;left:0;top:2px;width:30px;height:30px;border-radius:7px;background:var(--red);display:flex;align-items:center;justify-content:center}
.cred-icon i{width:12px;height:12px;border:2px solid var(--white);border-radius:50%}
.cred-name{position:absolute;left:43px;font-size:13px;font-weight:700;line-height:15px;color:var(--white)}
.cred-desc{position:absolute;left:43px;font-size:12px;line-height:14px;color:#e4e5f5}
.cred-sep{position:absolute;left:314px;width:180px;border-top:1.5px dashed var(--red)}

/* inside right */
.services-sub{left:591px;top:80px;width:400px;font-size:11.5px;line-height:14px;color:var(--muted)}
.service{position:absolute;left:593px;width:463px;height:54px}
.service-pill{position:absolute;left:0;top:0;width:155px;height:54px;border-radius:27px 4px 4px 27px;display:flex;align-items:center;padding-left:58px;font-size:12.5px;font-weight:700;line-height:15px;color:var(--white)}
.service-pill--navy{background:var(--navy)}
.service-pill--red{background:var(--red)}
.service-pill--dark{background:#141414}
.service-badge{position:absolute;left:2px;top:2px;width:50px;height:50px;border-radius:50%;background:var(--white);display:flex;align-items:center;justify-content:center}
.service-badge i{width:22px;height:22px;border-radius:50%;border:2px solid currentColor}
.service-desc{position:absolute;left:159px;top:0;width:304px;height:54px;border:2px solid var(--red);border-radius:4px;display:flex;align-items:center;padding:0 20px;font-size:12.5px;line-height:15px;color:var(--ink)}
.blueprint-band{left:515px;top:560px;width:585px;height:152px;background:var(--navy-deep)}
.work-photo{position:absolute;top:483px;width:140px;height:140px;border-radius:50%;border:3px solid var(--red);box-shadow:0 0 0 3px var(--white)}
</style>
</head>
<body>

<!-- Outside spread: back cover + front cover -->
<section class="spread spread--outside">
  <div class="sky-photo" role="img" aria-label="Blue sky with soft white clouds"></div>

  <svg class="frame-lines" width="1100" height="712" viewBox="0 0 1100 712">
    <polygon points="138,547 414,444 414,712 138,712" fill="#2b2d8f"/>
    <polyline points="292,277 414,316 414,444" fill="none" stroke="#2b2d8f" stroke-width="1.5"/>
    <polyline points="108,712 108,592 128,586" fill="none" stroke="#2b2d8f" stroke-width="1.5"/>
    <polyline points="677,297 677,133 763,104" fill="none" stroke="#2b2d8f" stroke-width="1.5"/>
    <polyline points="880,64 972,30 972,293" fill="none" stroke="#2b2d8f" stroke-width="1.5"/>
    <polygon points="759,385 972,307 972,482 759,482" fill="#2b2d8f"/>
  </svg>

  <!-- Back cover -->
  <div class="abs center quote-mark">&ldquo;</div>
  <p class="abs center quote-text">Brackenvale Roofing’s expertise and professionalism<br>made all the difference for our property.</p>
  <p class="abs center quote-author">Dana R., Property Manager</p>
  <p class="abs center script get-in-touch">Get in Touch</p>
  <p class="abs center ready">Ready to protect your property with<br>the best in roofing?</p>
  <div class="photo house-photo" role="img" aria-label="Modern two-storey house on a floating lawn island with trees"></div>
  <p class="abs center contact-title">Contact us today!</p>
  <div class="abs contact-icons"><span></span><span></span><span></span></div>
  <p class="abs center contact-line" style="top:612px">555.014.2280</p>
  <p class="abs center contact-line" style="top:635px">sales@brackenvaleroofing.com</p>
  <p class="abs center contact-line" style="top:658px">brackenvaleroofing.com</p>

  <!-- Front cover -->
  <div class="abs brand-square"></div>
  <p class="abs center brand-name">BRACKENVALE<br>ROOFING</p>
  <h1 class="abs center headline"><span class="dark">Protecting</span><br><span class="red">Apartment</span><br><span class="red">Communities</span></h1>
  <p class="abs center script with-script">with</p>
  <p class="abs center subhead">Precision Roofing<br>Solutions</p>
  <div class="building-photo abs" role="img" aria-label="Row of red-shingled townhouse apartments with white balconies"></div>
  <svg class="abs seal" viewBox="0 0 120 120">
    <circle cx="60" cy="60" r="58" fill="#9a9a9a"/>
    <circle cx="60" cy="60" r="50" fill="#3a3a3a"/>
    <circle cx="60" cy="60" r="46" fill="#111"/>
    <path d="M16 66 H104 A46 46 0 0 1 16 66 Z" fill="#b3141c"/>
  </svg>
  <p class="abs center seal-text">Your<br>Trusted<br>Partner for<br>Brackenvale<br>Roofing</p>

  <div class="abs feature" style="left:627px"><span class="feature-icon feature-icon--red"><i></i></span><span class="feature-label">Certified<br>Expertise</span></div>
  <div class="abs feature" style="left:751px"><span class="feature-icon feature-icon--navy"><i></i></span><span class="feature-label">Unmatched<br>Reliability</span></div>
  <div class="abs feature" style="left:890px"><span class="feature-icon feature-icon--red"><i></i></span><span class="feature-label">Industry-leading<br>Warranty</span></div>
  <p class="abs center site-url">www.<b>brackenvale</b>roofing.com</p>
</section>

<!-- Inside spread -->
<section class="spread spread--inside">
  <svg class="frame-lines" width="1100" height="712" viewBox="0 0 1100 712">
    <polyline points="295,122 295,80 509,0 509,270" fill="none" stroke="#2b2d8f" stroke-width="1.5" transform="translate(0,38)"/>
    <polygon points="295,363 509,285 509,712 295,712" fill="#2b2d8f"/>
  </svg>

  <h2 class="abs section-title" style="left:42px;top:34px">Our Roofing<br><span class="red">Solutions</span></h2>

  <div class="solution" style="top:122px">
    <div class="solution-photo" role="img" aria-label="Roofer working on a flat TPO roof" style="background:linear-gradient(160deg,#c9d3de,#4a4f57)"></div>
    <p class="solution-name blue" style="top:6px">TPO Roofing</p>
    <p class="solution-desc" style="top:26px">Energy-efficient and durable for large flat roofs.</p>
  </div>
  <div class="divider" style="top:226px"></div>
  <div class="solution" style="top:235px">
    <div class="solution-photo" role="img" aria-label="Close-up of membrane roofing on a building" style="background:linear-gradient(160deg,#e3c6a8,#8a5a3c)"></div>
    <p class="solution-name red" style="top:6px">EPDM Roofing</p>
    <p class="solution-desc" style="top:26px">Resilient against extreme weather with proven longevity.</p>
  </div>
  <div class="divider" style="top:342px"></div>
  <div class="solution" style="top:352px">
    <div class="solution-photo" role="img" aria-label="Worker installing PVC roofing" style="background:linear-gradient(160deg,#d7d7d7,#3b3d42)"></div>
    <p class="solution-name blue" style="top:6px">PVC Roofing</p>
    <p class="solution-desc" style="top:26px">Fire, chemical, and water-resistant for multifamily properties</p>
  </div>
  <div class="divider" style="top:457px"></div>
  <div class="solution" style="top:465px">
    <div class="solution-photo" role="img" aria-label="Hands laying asphalt shingles" style="background:linear-gradient(160deg,#8c7a66,#2e2b29)"></div>
    <p class="solution-name red" style="top:6px">Asphalt Shingles</p>
    <p class="solution-desc" style="top:26px">Versatile and cost-effective with curb appeal.</p>
  </div>
  <div class="divider" style="top:568px"></div>
  <div class="solution" style="top:574px">
    <div class="solution-photo" role="img" aria-label="House roof with fresh protective coating" style="background:linear-gradient(160deg,#9aa3ad,#3a3f45)"></div>
    <p class="solution-name blue" style="top:6px">Roof Coatings</p>
    <p class="solution-desc" style="top:26px">Extend the lifespan of existing roofs and reduce maintenance costs</p>
  </div>

  <h3 class="abs why-title">Why Choose<br><span class="red">Brackenvale Roofing?</span></h3>
  <p class="abs why-body">We specialize in delivering superior roofing services tailored to meet the needs of apartment communities. Our certified experts ensure your property’s roof is built to last.</p>

  <div class="cred" style="top:396px">
    <span class="cred-icon"><i></i></span>
    <p class="cred-name" style="top:0">Certified Roofing<br>Contractor</p>
    <p class="cred-desc" style="top:37px">Expert craftsmanship<br>guaranteed.</p>
  </div>
  <div class="cred-sep" style="top:477px"></div>
  <div class="cred" style="top:495px">
    <span class="cred-icon"><i></i></span>
    <p class="cred-name" style="top:0">20-Year NDL<br>Warranty</p>
    <p class="cred-desc" style="top:37px">Peace of mind with<br>long-term protection.</p>
  </div>
  <div class="cred-sep" style="top:575px"></div>
  <div class="cred" style="top:590px">
    <span class="cred-icon"><i></i></span>
    <p class="cred-name" style="top:0">Vendor<br>Credentialing<br>Compliance</p>
    <p class="cred-desc" style="top:52px">Approved with all<br>major platforms</p>
  </div>

  <h2 class="abs section-title" style="left:591px;top:34px">Our <span class="red">Services</span></h2>
  <p class="abs services-sub">We offer comprehensive roofing solutions for every stage of your roof’s lifecycle.</p>

  <div class="service" style="top:133px">
    <div class="service-pill service-pill--navy"><span class="service-badge" style="color:var(--navy)"><i></i></span>Roof<br>Repairs</div>
    <div class="service-desc">Fast, reliable fixes to extend roof life</div>
  </div>
  <div class="service" style="top:197px">
    <div class="service-pill service-pill--red"><span class="service-badge" style="color:var(--red)"><i></i></span>Roof<br>Inspections</div>
    <div class="service-desc">Thorough assessments to identify potential issues</div>
  </div>
  <div class="service" style="top:261px">
    <div class="service-pill service-pill--dark"><span class="service-badge" style="color:#141414"><i></i></span>Preventative<br>Maintenance</div>
    <div class="service-desc">Keep your roof in optimal condition year-round</div>
  </div>
  <div class="service" style="top:325px">
    <div class="service-pill service-pill--navy"><span class="service-badge" style="color:var(--navy)"><i></i></span>New Roof<br>Installations</div>
    <div class="service-desc">High-quality installations with certified materials</div>
  </div>
  <div class="service" style="top:388px">
    <div class="service-pill service-pill--red"><span class="service-badge" style="color:var(--red)"><i></i></span>Emergency<br>Services</div>
    <div class="service-desc">24/7 rapid response to urgent roofing issues</div>
  </div>

  <div class="abs blueprint-band" role="img" aria-label="Dark navy band with faint architectural line drawing of buildings"></div>
  <div class="work-photo" style="left:591px;background:linear-gradient(160deg,#c9a58a,#5a4a44)" role="img" aria-label="Roofer repairing shingles on a pitched roof"></div>
  <div class="work-photo" style="left:754px;background:linear-gradient(160deg,#e9e9e9,#8d8f94)" role="img" aria-label="Roofer working on a large commercial roof"></div>
  <div class="work-photo" style="left:919px;background:linear-gradient(160deg,#f1f2f4,#9aa0a8)" role="img" aria-label="Team installing roofing panels"></div>
</section>

</body>
</html>
```